I want a website to be designed for our new company, it's an import and export company for variety of things.

please see the attached Logo for our company and the Images for our different sections for our busienss

Target Market(s)

multiple

Coding

Coded - Design and coding required

Number of Pages Required

5+ page

Font styles to use
Sans Serif

Colors

Designer to choose colors to be used in the design.

Requirements
Must have
• KVR GLOBALINKS
• KVR globalinks Trading & Contracting provides various services. The Company offers infrastructure construction, oil, enegy and gas services, agricultural projects, real estate development, travel and tourism, and food processing and trading.
• Civil contracting for infrastructure, residential and heavy projects. Through its main subsidiaries; distribution of general food products, construction chemicals including corrosion inhibitors and electrical machinery; provides catering and travel agency services; ownership and operation of a school; offers human sources services including manpower supply.
• Drilling and Gold Mines Used Machinery, All Kinds of Construction Machinery, Drilling Machines are manufactured and sold.
Nice to have
• good designa and beautiful colours, it has too look professional

```html
<!DOCTYPE html>
<html lang="en">
<head>
<meta charset="utf-8">
<title>KVR Globalinks – Trading &amp; Contracting</title>
<link href="https://fonts.googleapis.com/css2?family=Open+Sans:wght@400;500;600;700;800&display=swap" rel="stylesheet">
<style>
:root{
  --maroon:#7b1b23;
  --green:#2c6a17;
  --gold:#f2a33a;
  --ink:#1f1f1f;
  --text:#555;
  --band:#ececec;
  --band-light:#f3f3f3;
  --shadow-grey:#8a8a8a;
  --line:#9a9a9a;
  --dark:#262626;
  --white:#fff;
}
*{margin:0;padding:0;box-sizing:border-box}
html,body{width:1200px;height:3334px;overflow:hidden}
body{position:relative;background:var(--white);font-family:'Open Sans',sans-serif;color:var(--ink)}
.abs{position:absolute}

/* hero */
.hero{left:0;top:0;width:1200px;height:663px}
.hero-photo{left:0;top:0;width:1200px;height:663px;background:linear-gradient(100deg,#5a3a2a 0%,#8a6a50 30%,#b7a88f 55%,#6b5443 80%,#3c2c22 100%)}
.hero-edge{left:0;top:600px;width:1200px;height:70px}
.logo-box{left:144px;top:0;width:212px;height:142px;background:#151515;display:flex;align-items:center;justify-content:center}
.logo-name{color:var(--white);font-weight:600;font-size:17px;letter-spacing:2px}
.nav{font-size:15px;font-weight:600;color:var(--white)}
.nav a{position:absolute;color:var(--white);text-decoration:none;white-space:nowrap}
.nav a.active{color:var(--gold)}
.search{left:1039px;top:25px}
.hero-title{left:146px;top:262px;font-size:44px;line-height:44px;font-weight:800;color:var(--white);text-shadow:0 2px 6px rgba(0,0,0,.45)}
.arrow{top:321px;width:44px;height:44px}

/* welcome */
.welcome-shadow{left:144px;top:750px;width:371px;height:306px;background:var(--shadow-grey)}
.welcome-photo{left:151px;top:742px;width:372px;height:307px;background:linear-gradient(160deg,#3d4a5e 0%,#c07a48 45%,#6b7585 70%,#2a2e36 100%)}
.section-title{font-size:35px;line-height:40px;font-weight:500;color:var(--maroon)}
.rule{height:3px;background:var(--line)}
.welcome-text{left:573px;top:852px;width:500px;font-size:15px;line-height:29px;color:var(--text)}
.btn{display:flex;align-items:center;justify-content:center;background:var(--green);color:var(--white);font-size:13px;font-weight:600;text-transform:uppercase}

/* services */
.band-trading{left:0;top:1161px;width:1200px;height:439px;background:var(--band)}
.band-contracting{left:0;top:1600px;width:1200px;height:434px;background:var(--band-light)}
.trading-shadow{left:608px;top:1145px;width:592px;height:432px;background:var(--shadow-grey)}
.trading-photo{left:616px;top:1137px;width:584px;height:432px;background:linear-gradient(180deg,#5e7aa6 0%,#9fb2cb 28%,#d8d8d8 40%,#7c7c7c 75%,#4a4a4a 100%)}
.contract-shadow{left:8px;top:1634px;width:584px;height:432px;background:var(--shadow-grey)}
.contract-photo{left:0;top:1626px;width:584px;height:431px;background:linear-gradient(110deg,#3a3530 0%,#6a5e55 40%,#9a958f 70%,#5a5550 100%)}
.photo-label{font-size:58px;font-weight:700;color:var(--white);text-shadow:0 2px 8px rgba(0,0,0,.5)}
.service-list{list-style:none;font-size:16px;font-weight:500;line-height:19px;color:var(--ink);text-transform:uppercase}
.service-list li{position:absolute;left:0;padding-left:40px;white-space:nowrap}
.service-list svg{position:absolute;left:0;top:-1px}

/* news */
.card-photo{top:2228px;width:296px;height:216px}
.card-body{top:2421px;width:272px;height:159px;background:var(--band);padding:18px 20px}
.card-title{font-size:19px;line-height:28.5px;color:#333}
.card-date{position:absolute;left:20px;top:120px;font-size:12px;color:#666}

/* contact */
.footer-band{left:0;top:3064px;width:1200px;height:270px;background:var(--dark)}
.contact-box{left:144px;top:2731px;width:911px;height:479px;background:var(--band-light)}
.field{border:1px solid #c8c8c8;background:var(--white);font-size:12px;color:#777;padding:0 15px;display:flex;align-items:center}
.field.msg{align-items:flex-start;padding-top:16px}
.footer-links{left:144px;top:3250px;font-size:12px;color:#bbb;word-spacing:2px}
.copyright{left:144px;top:3282px;font-size:12px;color:#bbb}
.social{top:3266px;width:20px;height:20px;border-radius:50%;background:#6e6e6e}
</style>
</head>
<body>

<header class="abs hero">
  <div class="abs hero-photo" role="img" aria-label="Photo: warehouse manager with a blue clipboard in front of tall storage racks"></div>
  <svg class="abs hero-edge" width="1200" height="70" viewBox="0 0 1200 70">
    <polygon points="0,20 1200,48 1200,70 0,70" fill="#b5b5b5"/>
    <polygon points="0,15 1200,45 1200,52 0,30" fill="#111"/>
    <polygon points="0,30 1200,52 1200,70 0,70" fill="#fff"/>
  </svg>
  <div class="abs logo-box"><span class="logo-name">KVR GLOBALINKS</span></div>
  <nav class="abs nav" style="left:0;top:24px">
    <a class="active" style="left:400px">HOME</a>
    <a style="left:480px">ABOUT US</a>
    <a style="left:589px">SERVICES</a>
    <a style="left:690px">NEWS</a>
    <a style="left:769px">CONTACT US</a>
    <a style="left:894px">MEMBER LOGIN</a>
  </nav>
  <svg class="abs search" width="15" height="15" viewBox="0 0 15 15"><circle cx="6" cy="6" r="4.5" stroke="#fff" stroke-width="2" fill="none"/><line x1="9.5" y1="9.5" x2="13.5" y2="13.5" stroke="#fff" stroke-width="2.4"/></svg>
  <h1 class="abs hero-title">CURABITUR RISUS ENIM<br>ANTE RHONCUS</h1>
  <svg class="abs arrow" style="left:53px" viewBox="0 0 44 44"><circle cx="22" cy="22" r="20" fill="#111" stroke="#fff" stroke-width="2.5"/><polyline points="25,13 16,22 25,31" fill="none" stroke="#fff" stroke-width="3"/></svg>
  <svg class="abs arrow" style="left:1102px" viewBox="0 0 44 44"><circle cx="22" cy="22" r="20" fill="#111" stroke="#fff" stroke-width="2.5"/><polyline points="19,13 28,22 19,31" fill="none" stroke="#fff" stroke-width="3"/></svg>
</header>

<section class="welcome">
  <div class="abs welcome-shadow"></div>
  <div class="abs welcome-photo" role="img" aria-label="Photo: cargo truck on a highway with a plane overhead and shipping containers at sunset"></div>
  <h2 class="abs section-title" style="left:573px;top:738px">Welcome to<br>KVR Globalinks</h2>
  <div class="abs rule" style="left:573px;top:834px;width:161px"></div>
  <p class="abs welcome-text">Phasellus metus diam, laoreet quis imperdiet sit amet, pharetra dignissim nisi. Proin quis dui at justo interdum facilisis tempor in lorem. Fusce quis rhoncus nisi. Donec venenatis dignissim erat vitae varius. Aliquam mattis nec orci in rutrum. Nullam sit amet viverra enim. Quisque pharetra erat et porta efficitur.</p>
  <a class="abs btn" style="left:573px;top:1017px;width:104px;height:39px">Read More</a>
</section>

<section class="services">
  <div class="abs band-trading"></div>
  <div class="abs band-contracting"></div>

  <ul class="abs service-list" style="left:144px;top:1223px">
    <li style="top:0"><svg width="24" height="22"><rect x="1" y="1" width="22" height="20" fill="none" stroke="#888"/><polyline points="10,6 15,11 10,16" fill="none" stroke="#555" stroke-width="1.3"/></svg>INFRASTRUCTURE CONSTRUCTION</li>
    <li style="top:48px"><svg width="24" height="22"><rect x="1" y="1" width="22" height="20" fill="none" stroke="#888"/><polyline points="10,6 15,11 10,16" fill="none" stroke="#555" stroke-width="1.3"/></svg>OIL</li>
    <li style="top:96px"><svg width="24" height="22"><rect x="1" y="1" width="22" height="20" fill="none" stroke="#888"/><polyline points="10,6 15,11 10,16" fill="none" stroke="#555" stroke-width="1.3"/></svg>ENEGY AND GAS SERVICES</li>
    <li style="top:144px"><svg width="24" height="22"><rect x="1" y="1" width="22" height="20" fill="none" stroke="#888"/><polyline points="10,6 15,11 10,16" fill="none" stroke="#555" stroke-width="1.3"/></svg>AGRICULTURAL PROJECTS</li>
    <li style="top:192px"><svg width="24" height="22"><rect x="1" y="1" width="22" height="20" fill="none" stroke="#888"/><polyline points="10,6 15,11 10,16" fill="none" stroke="#555" stroke-width="1.3"/></svg>REAL ESTATE DEVELOPMENT</li>
    <li style="top:240px"><svg width="24" height="22"><rect x="1" y="1" width="22" height="20" fill="none" stroke="#888"/><polyline points="10,6 15,11 10,16" fill="none" stroke="#555" stroke-width="1.3"/></svg>RRAVEL AND TOURISM</li>
    <li style="top:288px"><svg width="24" height="22"><rect x="1" y="1" width="22" height="20" fill="none" stroke="#888"/><polyline points="10,6 15,11 10,16" fill="none" stroke="#555" stroke-width="1.3"/></svg>FOOD PROCESSING AND TRADING</li>
  </ul>
  <div class="abs trading-shadow"></div>
  <div class="abs trading-photo" role="img" aria-label="Photo: aerial view of trucks parked at a logistics warehouse loading dock"></div>
  <span class="abs photo-label" style="left:808px;top:1182px">TRADING</span>

  <div class="abs contract-shadow"></div>
  <div class="abs contract-photo" role="img" aria-label="Photo: two businessmen shaking hands across an office desk"></div>
  <span class="abs photo-label" style="left:144px;top:1966px">CONTRACTING</span>
  <ul class="abs service-list" style="left:649px;top:1700px">
    <li style="top:0"><svg width="24" height="22"><rect x="1" y="1" width="22" height="20" fill="none" stroke="#888"/><polyline points="10,6 15,11 10,16" fill="none" stroke="#555" stroke-width="1.3"/></svg>DISTRIBUTION OF GENERAL FOOD PRODUCTS</li>
    <li style="top:48px"><svg width="24" height="22"><rect x="1" y="1" width="22" height="20" fill="none" stroke="#888"/><polyline points="10,6 15,11 10,16" fill="none" stroke="#555" stroke-width="1.3"/></svg>CONSTRUCTION CHEMICALS INCLUDING<br>CORROSION INHIBITORS AND ELECTRICAL<br>MACHINERY</li>
    <li style="top:134px"><svg width="24" height="22"><rect x="1" y="1" width="22" height="20" fill="none" stroke="#888"/><polyline points="10,6 15,11 10,16" fill="none" stroke="#555" stroke-width="1.3"/></svg>PROVIDES CATERING AND TRAVEL AGENCY<br>SERVICES</li>
    <li style="top:202px"><svg width="24" height="22"><rect x="1" y="1" width="22" height="20" fill="none" stroke="#888"/><polyline points="10,6 15,11 10,16" fill="none" stroke="#555" stroke-width="1.3"/></svg>OWNERSHIP AND OPERATION OF A SCHOOL</li>
    <li style="top:250px"><svg width="24" height="22"><rect x="1" y="1" width="22" height="20" fill="none" stroke="#888"/><polyline points="10,6 15,11 10,16" fill="none" stroke="#555" stroke-width="1.3"/></svg>OFFERS HUMAN SOURCES SERVICES INCLUDING<br>MANPOWER SUPPLY</li>
  </ul>
</section>

<section class="news">
  <h2 class="abs section-title" style="left:0;width:1200px;text-align:center;top:2139px">News</h2>
  <div class="abs rule" style="left:520px;top:2196px;width:160px"></div>

  <div class="abs card-photo" style="left:144px;background:linear-gradient(180deg,#c9cdd2 0%,#9a8e80 50%,#5c4a38 100%)" role="img" aria-label="Photo: mining dump trucks on a dusty quarry road"></div>
  <article class="abs card-body" style="left:156px"><p class="card-title">Phasellus condimentum vitae faucibus sollicitu din vel metus.</p><span class="card-date">18 JANUARY, 2020</span></article>

  <div class="abs card-photo" style="left:452px;background:linear-gradient(180deg,#3f7fc8 0%,#e8eef4 35%,#b58a3a 60%,#4d6a3a 100%)" role="img" aria-label="Photo: large bucket-wheel excavator under a blue sky"></div>
  <article class="abs card-body" style="left:464px"><p class="card-title">Proin rhoncus nulla vitae velit efficitur, a mollis ligula rutrum.</p><span class="card-date">18 JANUARY, 2020</span></article>

  <div class="abs card-photo" style="left:760px;background:linear-gradient(180deg,#4f88d0 0%,#c9dcf0 45%,#2d5f9a 70%,#1c4680 100%)" role="img" aria-label="Photo: offshore oil drilling platform at sea"></div>
  <article class="abs card-body" style="left:772px"><p class="card-title">Vivamus dolor sapien, sollicitudin nec pulvinar sit amet, vulputate.</p><span class="card-date">18 JANUARY, 2020</span></article>

  <a class="abs btn" style="left:548px;top:2611px;width:103px;height:40px">View All</a>
</section>

<footer>
  <div class="abs footer-band"></div>
  <svg class="abs" style="left:0;top:3060px" width="1200" height="40" viewBox="0 0 1200 40">
    <polygon points="0,0 1200,18 1200,34 0,10" fill="#000"/>
    <polygon points="0,0 1200,0 1200,18" fill="#fff"/>
  </svg>
  <div class="abs contact-box"></div>
  <h2 class="abs section-title" style="left:0;width:1200px;text-align:center;top:2798px">Contact Us</h2>
  <div class="abs rule" style="left:518px;top:2855px;width:162px"></div>
  <div class="abs field" style="left:259px;top:2884px;width:217px;height:39px">Name</div>
  <div class="abs field" style="left:491px;top:2884px;width:217px;height:39px">Email</div>
  <div class="abs field" style="left:723px;top:2884px;width:217px;height:39px">Phone</div>
  <div class="abs field msg" style="left:259px;top:2940px;width:681px;height:127px">Message</div>
  <a class="abs btn" style="left:548px;top:3096px;width:103px;height:40px">Submit</a>

  <p class="abs footer-links">Home &nbsp;|&nbsp; About Us &nbsp;|&nbsp; Services &nbsp;|&nbsp; News &nbsp;|&nbsp; Contact us &nbsp;|&nbsp; Member Login</p>
  <p class="abs copyright">Copyright &nbsp;©&nbsp; 2020 &nbsp;KVR Globalinks. &nbsp;All rights reserved.</p>
  <span class="abs social" style="left:990px"></span>
  <span class="abs social" style="left:1034px"></span>
</footer>

</body>
</html>
```